Request for Business Card Design

Hi. My name is Marlene, I am looking for a new business card design for my company, Quarrow Signal Instruments, LLC. I really like the design you did for Tarsel Venture and was hoping you could do something similar using our full logo and our mark. I am also open to any raised texture design using our mark. I have attached our full logo, which would need to be somewhere on the card, as well as the mark in both outline and full form, as well as our brand colors / guide. The card does not have to be white, as long as our logo and mark appear. I actually like darker colored business cards more, but am open to all options. If you are interested in working with me, please let me know. We would also take the business card design into letterhead design if you can do that.

```html
<!DOCTYPE html>
<html lang="en">
<head>
<meta charset="utf-8">
<title>Quarrow Signal Instruments – Business Card</title>
<link href="https://fonts.googleapis.com/css2?family=Montserrat:wght@400;500;600;700&display=swap" rel="stylesheet">
<style>
  :root {
    --page-bg: #e9e8e6;
    --card-black: #1b1b1c;
    --card-black-deep: #0e0e0f;
    --emboss-light: #7a7a7c;
    --emboss-mid: #3a3a3c;
    --brand-cyan: #1aa3cc;
    --text-white: #f4f4f4;
    --text-soft: #d9d9d9;
  }
  * { box-sizing: border-box; margin: 0; padding: 0; }
  html, body {
    width: 1200px; height: 786px; overflow: hidden;
    background: var(--page-bg);
    font-family: "Montserrat", sans-serif;
  }
  .stage {
    width: 1200px; height: 786px;
    display: flex; align-items: center; justify-content: center; gap: 40px;
  }
  .card {
    position: relative;
    width: 540px; height: 309px;
    border-radius: 4px;
    overflow: hidden;
    box-shadow: 0 10px 28px rgba(0,0,0,.22);
  }

  /* Front */
  .card-front { background: var(--card-black); }
  .brand {
    position: absolute; left: 46px; top: 52px;
    display: flex; align-items: center; gap: 18px;
  }
  .brand-dot {
    width: 62px; height: 62px; border-radius: 50%;
    background: var(--brand-cyan);
    flex: none;
  }
  .brand-name {
    color: var(--text-white);
    font-weight: 600; font-size: 25px; line-height: 1.08;
    letter-spacing: .04em; text-transform: uppercase;
    white-space: nowrap;
  }
  .person {
    position: absolute; right: 290px; top: 168px;
    text-align: right; white-space: nowrap;
  }
  .person-name {
    color: var(--brand-cyan); font-weight: 700; font-size: 21px; line-height: 1.1;
  }
  .person-role {
    color: var(--text-soft); font-weight: 400; font-size: 12px; margin-top: 3px;
  }
  .divider {
    position: absolute; left: 268px; top: 150px;
    width: 2px; height: 62px; background: var(--brand-cyan);
  }
  .contact {
    position: absolute; left: 288px; top: 140px;
    list-style: none;
  }
  .contact li {
    display: flex; align-items: center; gap: 9px;
    color: var(--text-white); font-size: 12px; line-height: 24px;
    white-space: nowrap;
  }
  .contact svg { width: 12px; height: 12px; fill: var(--brand-cyan); flex: none; }
  .address-band {
    position: absolute; left: 0; right: 0; bottom: 22px;
    height: 38px; background: var(--brand-cyan);
    display: flex; align-items: center; padding-left: 120px;
    color: var(--text-white); font-size: 13px; font-weight: 500;
    white-space: nowrap;
  }
  .band-tab {
    position: absolute; right: 36px; bottom: 59px;
    width: 76px; height: 34px; background: var(--brand-cyan);
    border-radius: 8px 8px 0 0;
    display: flex; align-items: center; justify-content: center;
  }
  .band-dot {
    width: 22px; height: 22px; border-radius: 50%; background: var(--card-black);
  }

  /* Back */
  .card-back { background: var(--card-black-deep); }
  .raised-texture {
    position: absolute; inset: 0;
    background: linear-gradient(115deg, var(--emboss-light) 0%, var(--emboss-mid) 32%, #1c1c1d 62%, var(--card-black-deep) 100%);
  }
  .back-brand {
    position: absolute; right: 30px; top: 132px;
    display: flex; align-items: center; gap: 12px;
  }
  .back-brand .brand-dot { width: 34px; height: 34px; }
  .back-brand .brand-name { font-size: 15px; }
</style>
</head>
<body>
<main class="stage">

  <section class="card card-front" aria-label="Business card front">
    <div class="brand">
      <span class="brand-dot"></span>
      <p class="brand-name">Quarrow<br>Signal Instruments</p>
    </div>

    <div class="person">
      <p class="person-name">Marlene Ashford</p>
      <p class="person-role">Owner</p>
    </div>

    <span class="divider"></span>

    <ul class="contact">
      <li>
        <svg viewBox="0 0 24 24" aria-hidden="true"><path d="M6.6 10.8a15.1 15.1 0 0 0 6.6 6.6l2.2-2.2a1 1 0 0 1 1-.25 11.4 11.4 0 0 0 3.6.57 1 1 0 0 1 1 1V20a1 1 0 0 1-1 1A17 17 0 0 1 3 4a1 1 0 0 1 1-1h3.5a1 1 0 0 1 1 1c0 1.25.2 2.45.57 3.57a1 1 0 0 1-.25 1z"/></svg>
        +001 555 210 3398
      </li>
      <li>
        <svg viewBox="0 0 24 24" aria-hidden="true"><path d="M2 5h20v14H2z M4 7v.4l8 5 8-5V7l-8 5z" fill-rule="evenodd"/></svg>
        info@quarrowsignal.com
      </li>
      <li>
        <svg viewBox="0 0 24 24" aria-hidden="true"><path d="M12 2a10 10 0 1 0 0 20 10 10 0 0 0 0-20zm6.9 9h-3a15 15 0 0 0-1.3-5.6A8 8 0 0 1 18.9 11zM12 4.1c.9 1.3 1.7 3.8 1.9 6.9h-3.8c.2-3.1 1-5.6 1.9-6.9zM9.4 5.4A15 15 0 0 0 8.1 11h-3a8 8 0 0 1 4.3-5.6zM5.1 13h3a15 15 0 0 0 1.3 5.6A8 8 0 0 1 5.1 13zm6.9 6.9c-.9-1.3-1.7-3.8-1.9-6.9h3.8c-.2 3.1-1 5.6-1.9 6.9zm2.6-1.3a15 15 0 0 0 1.3-5.6h3a8 8 0 0 1-4.3 5.6z"/></svg>
        www.quarrowsignal.com
      </li>
    </ul>

    <div class="band-tab"><span class="band-dot"></span></div>
    <div class="address-band">1180 Harbor Mill Road, Eastbrook, CO 80000</div>
  </section>

  <section class="card card-back" aria-label="Business card back">
    <div class="raised-texture" role="img" aria-label="Raised glossy repeat pattern of the company mark across the whole card, light at the left fading to black"></div>
    <div class="back-brand">
      <span class="brand-dot"></span>
      <p class="brand-name">Quarrow<br>Signal Instruments</p>
    </div>
  </section>

</main>
</body>
</html>
```